Aerial Imaging and photgraphy business card

Design a business card with eye catching aerial photo of country side / landscape with a drone in the foreground.
Also contact details.

Target Market(s)

Aerial Imaging photography

Industry/Entity Type

Advertising

Contact Information for Business Card

Rowland
0412965203
Website http://www.skywardvistaphoto.com.au/
email address : skywardvistaphoto.com.au

Colors
e8f1ca
cadf82
9bcb3c
33a6d7
85cae6
cee9f5

Requirements
Must have
• High res photo
• Korvane drone in the foreground Either T4200 and korvane Glidewing or both
Nice to have
• high resolution landscape country photo on the front of the card with a Korvane T4200 drone in the foreground.

```html
<!DOCTYPE html>
<html lang="en">
<head>
<meta charset="utf-8">
<title>Skyward Vista Photo – Business Card</title>
<link href="https://fonts.googleapis.com/css2?family=Roboto:wght@400;500;700&display=swap" rel="stylesheet">
<style>
  :root{
    --bg:#e4e4e4;
    --card:#ffffff;
    --ink:#333333;
    --ink-soft:#555555;
    --green:#8cc63f;
    --green-dark:#3f9a2c;
    --blue:#1d9fd6;
    --blue-deep:#1c4f66;
    --sky:#cfe3f0;
    --field:#6f8f48;
  }
  *{margin:0;padding:0;box-sizing:border-box}
  html,body{width:1200px;height:1200px;overflow:hidden;background:var(--bg);font-family:"Roboto",Arial,sans-serif}
  .canvas{position:relative;width:1200px;height:1200px}
  .card{position:absolute;left:220px;width:760px;height:434px;border-radius:14px;overflow:hidden;box-shadow:0 4px 14px rgba(0,0,0,.18)}
  .card--front{top:136px}
  .card--back{top:630px;background:var(--card)}
  .photo{width:100%;height:100%;background:linear-gradient(180deg,#bcd6ea 0%,var(--sky) 30%,#dfe6e8 45%,#8fae6a 62%,var(--field) 78%,#3e5a2c 100%)}
  .brand{position:absolute;left:46px;top:150px;display:flex;align-items:center;gap:12px}
  .brand__mark{width:26px;height:26px;border-radius:50%;background:var(--green)}
  .brand__name{font-size:30px;font-weight:700;color:var(--ink);letter-spacing:.5px}
  .person{position:absolute;right:50px;top:40px;text-align:right}
  .person__name{font-size:27px;font-weight:700;color:var(--ink)}
  .person__role{font-size:15px;color:var(--ink-soft);margin-top:4px}
  .contacts{position:absolute;right:50px;top:122px;text-align:right;font-size:18px;color:var(--ink);line-height:26px}
  .contacts li{list-style:none;display:flex;justify-content:flex-end;align-items:center;gap:10px}
  .contacts svg{width:15px;height:15px}
  .contacts .web-accent{color:var(--green-dark)}
  .address{position:absolute;left:40px;bottom:40px;font-size:18px;color:var(--ink);line-height:24px}
  .bands{position:absolute;left:0;bottom:0;width:760px;height:140px}
</style>
</head>
<body>
<div class="canvas">
  <section class="card card--front">
    <div class="photo" role="img" aria-label="Aerial photograph of green countryside and a lake with a camera drone flying in the foreground"></div>
  </section>

  <section class="card card--back">
    <div class="brand">
      <span class="brand__mark"></span>
      <span class="brand__name">Skyward Vista Photo</span>
    </div>

    <div class="person">
      <div class="person__name">Rowland Hale</div>
      <div class="person__role">Managing Director</div>
    </div>

    <ul class="contacts">
      <li>0412965203
        <svg viewBox="0 0 16 16"><path fill="#1d9fd6" d="M3 2h3l1 4-2 1a9 9 0 0 0 4 4l1-2 4 1v3a1 1 0 0 1-1 1A12 12 0 0 1 2 3a1 1 0 0 1 1-1z"/></svg></li>
      <li>hello@skywardvistaphoto.com.au
        <svg viewBox="0 0 16 16"><rect x="1" y="3" width="14" height="10" rx="1" fill="#1d9fd6"/><path d="M1 4l7 5 7-5" stroke="#fff" stroke-width="1.3" fill="none"/></svg></li>
      <li><span>www.<span class="web-accent">skywardvistaphoto</span>.com.au</span>
        <svg viewBox="0 0 16 16"><circle cx="8" cy="8" r="7" fill="#1d9fd6"/><path d="M1 8h14M8 1c-3 4-3 10 0 14M8 1c3 4 3 10 0 14" stroke="#fff" stroke-width="1" fill="none"/></svg></li>
    </ul>

    <div class="address">Marrowvale<br>NSW 2591, Australia</div>

    <svg class="bands" viewBox="0 0 760 140" preserveAspectRatio="none" aria-hidden="true">
      <defs>
        <linearGradient id="blueBand" x1="0" y1="0" x2="1" y2="0">
          <stop offset="0" stop-color="#1c4f66"/>
          <stop offset=".55" stop-color="#1d9fd6"/>
          <stop offset="1" stop-color="#1c4f66"/>
        </linearGradient>
      </defs>
      <path d="M0 132 L480 132 L520 118 L760 118 L760 140 L0 140 Z" fill="#8cc63f"/>
      <path d="M512 40 L760 40 L760 118 L540 118 Z" fill="url(#blueBand)"/>
    </svg>
  </section>
</div>
</body>
</html>
```